Website for a company offering full serivce charging solutions for electric cars

The company "tanu-werk" (english: "tanu-works") offering all-in-one-solutions for charging infrastructure for electric mobility.

There are four products:
1- Wallboxes for single-family homes
2- Solutions for property devloper/-management for property parking space
3- All-in-one-charging solution for municipalities/communities
4- Solutions for tourism/hotels/holiday appartments

The Website structure:
1. Main Page
2.1. Product Page Single Homes
2.2. Product Page Property Management / Parking
2.3. Product Page Municipality
2.4. Product Page Tourism
3. Contact Form / Request for information
4. Imprint / Legal

The Website should be built on Wordpress with a powerful possibility to simply add/modify specific landing pages.

We would like you to implement the website later and also maintain it if possible, but we would be able to do minor modifications by ourselfs (for A/B-Testing)

The website should be clear and simple, easy to understand.
Target group is mainly B2C without deeper knowledge of that topic.

It should suggest, that we will provide a very simple way to get the charging infrastructure done.

We need a contact form, maybe we will use Hubspot later.

Attached you will find a draft of the main page and a landing page (for 2.2) - it is just the content, please ignore the design. We would love to let you create a suitable design.
Also you will find some drafts a bit different for the same story.

I added also a few stock photos, but they don't need to be used! If you have better ideas, you are welcome!

Industry/Entity Type

Charging/Electric mobility

Number of Pages Required

2 page

Font styles to use
Sans Serif

Requirements
Must have
• Based on Wordpress, and the designer should be able to implement it on Wordpress on a later step

```html
<!DOCTYPE html>
<html lang="de">
<head>
<meta charset="utf-8">
<title>tanu-werk – Ladeinfrastruktur für Elektromobilität</title>
<link href="https://fonts.googleapis.com/css2?family=Exo+2:wght@600;700&family=Poppins:wght@400;500;600&display=swap" rel="stylesheet">
<style>
:root{
  --pink:#e3168f;
  --violet:#7a5fcb;
  --grad:linear-gradient(90deg,var(--pink),var(--violet));
  --ink:#1c1d3b;
  --text:#2b2b3a;
  --blush:#fbeef6;
  --white:#ffffff;
}
*{box-sizing:border-box;margin:0;padding:0}
html,body{width:1200px;height:2392px;overflow:hidden}
body{font-family:"Poppins",sans-serif;color:var(--text);background:var(--white);position:relative}
.heading{font-family:"Exo 2",sans-serif;font-weight:700;color:var(--ink)}
.btn{display:inline-flex;align-items:center;justify-content:center;background:var(--grad);color:var(--white);border-radius:20px;font-weight:500;text-decoration:none;position:absolute;white-space:nowrap}

/* header */
.site-header{position:absolute;top:0;left:0;width:1200px;height:87px;background:var(--white)}
.brand{position:absolute;left:124px;top:28px;display:flex;align-items:center;gap:10px;font-family:"Poppins",sans-serif;font-weight:600;font-size:21px;color:var(--ink);white-space:nowrap}
.brand-dot{width:16px;height:16px;border-radius:50%;background:var(--pink);flex:none}
.main-nav{position:absolute;left:411px;top:35px;display:flex;gap:19px;font-size:13px;color:var(--ink);white-space:nowrap}
.main-nav .active{position:relative}
.main-nav .active::after{content:"";position:absolute;left:0;right:0;bottom:-8px;height:2px;background:var(--grad)}
.header-call{left:880px;top:25px;width:196px;height:37px;font-size:12px;font-weight:600;gap:8px;padding-left:6px;justify-content:flex-start}
.call-icon{width:26px;height:26px;border-radius:50%;background:var(--white);display:flex;align-items:center;justify-content:center}

/* hero */
.hero{position:absolute;top:87px;left:0;width:1200px;height:563px;background:linear-gradient(180deg,#3b4048 0%,#5a5e5f 45%,#6d6a62 75%,#8a8a86 100%)}
.hero-title{position:absolute;top:130px;left:0;width:1200px;text-align:center;color:var(--white);font-size:40px;line-height:50px}
.hero-cta{left:491px;top:249px;width:217px;height:41px;font-size:13.5px;font-weight:600}

/* partner */
.partner-title{position:absolute;left:163px;top:724px;font-size:31px}
.partner-copy{position:absolute;left:163px;top:776px;width:420px;font-size:13.5px;line-height:21.7px;letter-spacing:.3px}
.partner-copy p+p{margin-top:16px}
.partner-btn{left:164px;top:1058px;width:135px;height:38px;font-size:15px}
.partner-photo{position:absolute;left:633px;top:708px;width:405px;height:412px;border-radius:22px;background:linear-gradient(135deg,#f0b14c 0%,#c98a48 35%,#5e5148 65%,#cfd3d8 100%)}

/* solutions */
.solutions{position:absolute;top:1209px;left:0;width:1200px;height:768px;background:linear-gradient(180deg,var(--blush),#f8f3fa)}
.solutions-title{position:absolute;top:95px;left:0;width:1200px;text-align:center;font-size:30px;line-height:40px}
.tabs{position:absolute;top:202px;left:0;width:1200px;display:flex;justify-content:center;gap:20px}
.tab{height:38px;padding:0 19px;border-radius:20px;border:1.5px solid var(--pink);display:flex;align-items:center;font-family:"Exo 2",sans-serif;font-weight:600;font-size:17px;color:var(--ink)}
.tab.active{background:var(--grad);color:var(--white);border-color:transparent}
.home-art{position:absolute;left:60px;top:320px;width:526px;height:345px;border-radius:6px;background:linear-gradient(160deg,#e3e4ee 0%,#c5c8d6 45%,#7bc17e 80%,#ee5cbc 100%)}
.offer{position:absolute;left:625px;top:300px;width:400px}
.offer-title{font-size:25px}
.offer-list{list-style:none;margin-top:16px}
.offer-list li{display:flex;gap:14px;font-size:13.5px;line-height:20.5px;margin-bottom:14px;color:var(--ink)}
.offer-list svg{flex:none;margin-top:3px}
.offer-btn{left:625px;top:642px;width:135px;height:38px;font-size:15px}

/* footer */
.site-footer{position:absolute;top:1977px;left:0;width:1200px;height:379px}
.foot-title{position:absolute;top:88px;font-family:"Exo 2",sans-serif;font-weight:700;font-size:16px;color:var(--ink)}
.quick-links{position:absolute;left:163px;top:130px;list-style:none;font-size:13px;color:var(--ink)}
.quick-links li{height:37.5px}
.contact-item{position:absolute;left:439px;display:flex;gap:12px;font-size:14px;color:var(--ink);line-height:20px}
.contact-icon{width:34px;height:34px;border-radius:50%;background:var(--grad);display:flex;align-items:center;justify-content:center;flex:none}
.contact-item strong{font-weight:500;font-size:16px;display:block}
.foot-brand{position:absolute;left:766px;top:168px;width:300px;display:flex;align-items:center;justify-content:center;gap:10px;font-family:"Poppins",sans-serif;font-weight:600;font-size:34px;line-height:44px;color:var(--ink);white-space:nowrap}
.foot-brand .brand-dot{width:20px;height:20px}
.social{position:absolute;left:843px;top:2209px;display:flex;gap:16px}
.social span{width:38px;height:38px;border-radius:50%;background:var(--grad);display:block}
.copyright{position:absolute;top:2356px;left:0;width:1200px;height:36px;background:var(--grad);color:var(--white);font-size:13px;display:flex;align-items:center;justify-content:center}
</style>
</head>
<body>

<header class="site-header">
  <div class="brand"><span class="brand-dot"></span>tanu-werk.de</div>
  <nav class="main-nav">
    <span class="active">Lösungen</span><span>Unternehmen</span><span>Dienstleistungen</span><span>Karriere</span><span>Kontakt</span>
  </nav>
  <a class="btn header-call"><span class="call-icon"><svg width="13" height="13" viewBox="0 0 24 24"><path fill="#e3168f" d="M6.6 10.8a15 15 0 0 0 6.6 6.6l2.2-2.2c.3-.3.7-.4 1-.2 1.1.4 2.3.6 3.6.6.6 0 1 .4 1 1V20c0 .6-.4 1-1 1A17 17 0 0 1 3 4c0-.6.4-1 1-1h3.5c.6 0 1 .4 1 1 0 1.3.2 2.5.6 3.6.1.3 0 .7-.2 1z"/></svg></span>123 456 7890 (Zollfrei)</a>
</header>

<section class="hero" role="img" aria-label="Foto: modernes Wohnhaus in der Dämmerung, ein weißes Elektroauto lädt an einer Ladesäule">
  <h1 class="heading hero-title" style="color:#fff">All-in-One-Lösungen Für Ladeinfrastruktur<br>Für Elektromobilität Anzubieten.</h1>
  <a class="btn hero-cta">Kontaktiere Uns Heute</a>
</section>

<h2 class="heading partner-title">Tanu-werk Ist Ihr Partner</h2>
<div class="partner-copy">
  <p>wenn das Laden nicht nur einfach, sondern die Umsetzung auch aus einer Hand kommen soll Wir bieten Lösungen sowohl für Privatkunden, Geschäfts- kunden als auch Kommunen an, die schnell, fair und ohne Eigenleistung zu einer smarten Ladelösung für E-Fahrzeuge kommen möchten.</p>
  <p>Von der Beratung, über die Installation, Inbetriebnahme bis zur Abrechnung und Wartung bekommen Sie bei tanu-werk alles aus einer Hand. Auf Wunsch vermieten wir auch die Ladetechnik und übernehmen im gewerblichen Bereich die direkte Abrechnung mit dem Nutzer.</p>
</div>
<a class="btn partner-btn">Alle Ansehen</a>
<div class="partner-photo" role="img" aria-label="Foto: Frau mit Smartphone lädt ihr Elektroauto bei Sonnenuntergang"></div>

<section class="solutions">
  <h2 class="heading solutions-title">Fragen Sie Uns Nach Der Auf Ihre Individuellen<br>Bedürfnisse Zugeschnittenen Lösung</h2>
  <div class="tabs">
    <span class="tab active">Als Privatkunde</span><span class="tab">Als Geschäftskunde</span><span class="tab">Als Kommune</span>
  </div>
  <div class="home-art" role="img" aria-label="Illustration: Einfamilienhaus mit Solardach, pinkes Elektroauto an der Wallbox, Bäume und ein Bewohner"></div>
  <div class="offer">
    <h3 class="heading offer-title">Als Privatkunde</h3>
    <ul class="offer-list">
      <li><svg width="16" height="14" viewBox="0 0 16 14"><path d="M1 7h5M6 2h5a4 4 0 0 1 0 10H6zM2 4h4M2 10h4" fill="none" stroke="#b24bb8" stroke-width="1.6"/></svg>Bestandsanalyse mit umfangreicher Beratung über die Möglichkeiten der Umsetzung</li>
      <li><svg width="16" height="14" viewBox="0 0 16 14"><path d="M1 7h5M6 2h5a4 4 0 0 1 0 10H6zM2 4h4M2 10h4" fill="none" stroke="#b24bb8" stroke-width="1.6"/></svg>Prüfung und Übernahme der Anmeldung verfügbarer Fördermöglichkeiten</li>
      <li><svg width="16" height="14" viewBox="0 0 16 14"><path d="M1 7h5M6 2h5a4 4 0 0 1 0 10H6zM2 4h4M2 10h4" fill="none" stroke="#b24bb8" stroke-width="1.6"/></svg>Auswahl an smarten Wallbox Lösungen, passend für Ihr Fahrzeug und Ihre Bedürfnisse</li>
      <li><svg width="16" height="14" viewBox="0 0 16 14"><path d="M1 7h5M6 2h5a4 4 0 0 1 0 10H6zM2 4h4M2 10h4" fill="none" stroke="#b24bb8" stroke-width="1.6"/></svg>Installation inkl. aller notwendigen Materialien und Tätigkeiten (Durchbrüche, Erdarbeiten, etc.)</li>
      <li><svg width="16" height="14" viewBox="0 0 16 14"><path d="M1 7h5M6 2h5a4 4 0 0 1 0 10H6zM2 4h4M2 10h4" fill="none" stroke="#b24bb8" stroke-width="1.6"/></svg>Inbetriebnahme und Einweisung in die Ladetechnik</li>
      <li><svg width="16" height="14" viewBox="0 0 16 14"><path d="M1 7h5M6 2h5a4 4 0 0 1 0 10H6zM2 4h4M2 10h4" fill="none" stroke="#b24bb8" stroke-width="1.6"/></svg>Jährlich technische Wartung nach DGUV3</li>
    </ul>
  </div>
  <a class="btn offer-btn">Alle Ansehen</a>
</section>

<footer class="site-footer">
  <h4 class="foot-title" style="left:163px">Schnelle Links</h4>
  <ul class="quick-links">
    <li>AGB</li><li>Datenschutzerklärung</li><li>Impressum</li><li>Kontakt</li><li>Karriere</li><li>FAQs</li>
  </ul>
  <h4 class="foot-title" style="left:441px">Kontaktangaben</h4>
  <div class="contact-item" style="top:126px">
    <span class="contact-icon"><svg width="14" height="16" viewBox="0 0 24 24"><path fill="#fff" d="M12 2a7 7 0 0 0-7 7c0 5 7 13 7 13s7-8 7-13a7 7 0 0 0-7-7zm0 9.5A2.5 2.5 0 1 1 12 6.5a2.5 2.5 0 0 1 0 5z"/></svg></span>
    <div><strong>Ein Kleid</strong>12 Gebäude, Straße, Stadt,<br>Bundesland</div>
  </div>
  <div class="contact-item" style="top:210px">
    <span class="contact-icon"><svg width="14" height="14" viewBox="0 0 24 24"><path fill="#fff" d="M6.6 10.8a15 15 0 0 0 6.6 6.6l2.2-2.2c.3-.3.7-.4 1-.2 1.1.4 2.3.6 3.6.6.6 0 1 .4 1 1V20c0 .6-.4 1-1 1A17 17 0 0 1 3 4c0-.6.4-1 1-1h3.5c.6 0 1 .4 1 1 0 1.3.2 2.5.6 3.6.1.3 0 .7-.2 1z"/></svg></span>
    <div style="padding-top:3px">123 456 7890 (Zollfrei)</div>
  </div>
  <div class="contact-item" style="top:260px">
    <span class="contact-icon"><svg width="14" height="12" viewBox="0 0 24 20"><path fill="#fff" d="M2 2h20v2l-10 7L2 4zm0 5 10 7 10-7v11H2z"/></svg></span>
    <div style="padding-top:3px;padding-left:6px">info@tanu-werk.de.com</div>
  </div>
  <div class="foot-brand"><span class="brand-dot"></span>tanu-werk.de</div>
</footer>
<div class="social" aria-label="Soziale Netzwerke"><span></span><span></span><span></span></div>
<div class="copyright">Urheberrecht © 2022 tanu-werk.de. Alle Rechte vorbehalten.</div>

</body>
</html>
```